Birchline Septic Solutions

Would like to see some single sided ones but would also like to see some double sided with one sided only being the logo. Owners name is Colin Vandro. Phone number is 555-214-0387
Services are pumping, inspections, installs, and repairs

Contact Information for Business Card

555-241-0387 Colin Vandro Larkdale, OH

```html
<!DOCTYPE html>
<html lang="en">
<head>
<meta charset="utf-8">
<title>Birchline Septic Solutions – Business Card</title>
<link rel="stylesheet" href="https://fonts.googleapis.com/css2?family=Open+Sans:wght@400;600;700&display=swap">
<style>
  :root {
    --backdrop: #242424;
    --card: #1f1f23;
    --ink: #ffffff;
    --teal: #26b5ad;
    --shadow: rgba(0, 0, 0, 0.55);
  }
  * { margin: 0; padding: 0; box-sizing: border-box; }
  html, body {
    width: 1200px;
    height: 779px;
    overflow: hidden;
    background: var(--backdrop);
    font-family: "Open Sans", Arial, sans-serif;
    color: var(--ink);
  }
  .canvas {
    position: relative;
    width: 1200px;
    height: 779px;
    display: flex;
    justify-content: center;
    align-items: center;
    gap: 64px;
  }
  .card {
    position: relative;
    width: 350px;
    height: 612px;
    background: var(--card);
    border-radius: 22px;
    box-shadow: 0 18px 40px var(--shadow);
    overflow: hidden;
  }

  /* Front: logo side */
  .card--front .brand-mark {
    position: absolute;
    left: 50%;
    top: 50%;
    transform: translate(-50%, -50%) rotate(-90deg);
    text-align: center;
    white-space: nowrap;
    font-weight: 700;
    color: var(--ink);
  }
  .brand-mark__name {
    display: block;
    font-size: 62px;
    line-height: 1;
    letter-spacing: 1px;
  }
  .brand-mark__tagline {
    display: block;
    margin-top: 10px;
    font-size: 22px;
    letter-spacing: 7px;
    text-transform: uppercase;
  }

  /* Back: contact side */
  .card--back .brand-header {
    position: absolute;
    top: 72px;
    left: 0;
    right: 0;
    text-align: center;
    font-weight: 700;
    color: var(--ink);
  }
  .brand-header__name {
    display: block;
    font-size: 42px;
    line-height: 1;
  }
  .brand-header__tagline {
    display: block;
    margin-top: 8px;
    font-size: 13px;
    letter-spacing: 4px;
    text-transform: uppercase;
  }
  .contact {
    position: absolute;
    top: 300px;
    left: 0;
    right: 0;
    text-align: center;
  }
  .contact__name {
    font-size: 26px;
    font-weight: 700;
    line-height: 1.1;
  }
  .contact__name .first { color: var(--teal); }
  .contact__name .last { color: var(--ink); }
  .contact__town {
    font-size: 14px;
    font-weight: 400;
    margin-top: 2px;
  }
  .contact__phone-icon {
    display: block;
    margin: 10px auto 4px;
  }
  .contact__phone {
    font-size: 22px;
    font-weight: 400;
    letter-spacing: 0.5px;
  }
  .services {
    margin-top: 18px;
  }
  .services__badge {
    display: inline-block;
    background: var(--teal);
    color: var(--ink);
    font-size: 13px;
    font-weight: 600;
    letter-spacing: 0.5px;
    padding: 4px 22px;
    border-radius: 50%;
  }
  .services__arrow { display: block; margin: 2px auto 4px; }
  .services__list {
    list-style: none;
    font-size: 15px;
    line-height: 1.3;
  }
</style>
</head>
<body>
  <main class="canvas">
    <section class="card card--front" aria-label="Card front">
      <div class="brand-mark">
        <span class="brand-mark__name">Birchline</span>
        <span class="brand-mark__tagline">Septic Solutions</span>
      </div>
    </section>

    <section class="card card--back" aria-label="Card back">
      <div class="brand-header">
        <span class="brand-header__name">Birchline</span>
        <span class="brand-header__tagline">Septic Solutions</span>
      </div>

      <div class="contact">
        <p class="contact__name"><span class="first">Colin</span> <span class="last">Vandro</span></p>
        <p class="contact__town">Larkdale, OH</p>
        <svg class="contact__phone-icon" width="34" height="40" viewBox="0 0 34 40" aria-hidden="true">
          <circle cx="17" cy="13" r="12" fill="var(--teal)"/>
          <path d="M12.5 8.5c.6-.6 1.4-.5 1.8.1l1.2 1.8c.3.5.2 1.1-.2 1.5l-.8.7c.7 1.5 1.8 2.6 3.3 3.3l.7-.8c.4-.4 1-.5 1.5-.2l1.8 1.2c.6.4.7 1.2.1 1.8l-.9.9c-.7.7-1.9.8-3 .3-2.6-1.2-4.6-3.2-5.8-5.8-.5-1.1-.4-2.3.3-3z" fill="var(--ink)"/>
          <path d="M17 26v7" stroke="var(--teal)" stroke-width="2"/>
          <path d="M12 31l5 7 5-7z" fill="var(--teal)"/>
        </svg>
        <p class="contact__phone">555-241-0387</p>

        <div class="services">
          <span class="services__badge">SERVICES</span>
          <svg class="services__arrow" width="14" height="12" viewBox="0 0 14 12" aria-hidden="true">
            <path d="M2 2l5 8 5-8z" fill="var(--teal)"/>
          </svg>
          <ul class="services__list">
            <li>Installs</li>
            <li>Pumping</li>
            <li>Inspections</li>
            <li>And Repairs</li>
          </ul>
        </div>
      </div>
    </section>
  </main>
</body>
</html>
```